web Design for Architecture and Interior Design Firm

This is a complete redesign of an architecture and interior design firm.( http://www.qlbrankworks.com )
We have established a new look-n-feel for them and need to apply it to the new site/new architecture. Wireframes attached with logo and PDF of new brochure.
This will require a quck turn-around. The client is expecting a very modern design with web 2.0 in mind.
Again very quick turn-around! If you cannot commit to a Friday deliverable, do not bid! Must be completed by no later than Friday!

```html
<!DOCTYPE html>
<html lang="en">
<head>
<meta charset="utf-8">
<title>Qlbrank Works — Design Studios</title>
<link rel="stylesheet" href="https://fonts.googleapis.com/css2?family=Jost:wght@400;500&family=Arimo:wght@400;700&display=swap">
<style>
  :root {
    --bg-brown: #6a5e4b;
    --bg-brown-light: #776b57;
    --panel: #ffffff;
    --ink-brown: #5e5444;
    --ink: #444444;
    --accent-red: #c8102e;
    --nav-grey: #555555;
    --nav-divider: #9a9a9a;
    --rule: #8a8a8a;
    --caption-bg: rgba(60, 50, 40, 0.72);
  }
  * { margin: 0; padding: 0; box-sizing: border-box; }
  html, body { width: 1200px; height: 844px; overflow: hidden; }
  body {
    background: var(--bg-brown);
    font-family: "Arimo", Arial, sans-serif;
    position: relative;
  }
  .backdrop-drawing {
    position: absolute; left: 0; top: 0; width: 159px; height: 844px;
    background: linear-gradient(160deg, var(--bg-brown-light), var(--bg-brown));
  }
  .page {
    position: absolute; left: 159px; top: 0; width: 882px; height: 778px;
    background: var(--panel);
  }

  /* Brand */
  .brand {
    position: absolute; left: 61px; top: 40px;
    display: flex; align-items: center; gap: 10px;
    font-family: "Jost", sans-serif;
    font-size: 30px; font-weight: 500; line-height: 1;
    color: var(--ink-brown); letter-spacing: 0.5px;
  }
  .brand-mark { width: 12px; height: 12px; background: var(--accent-red); flex: none; }

  /* Navigation */
  .main-nav {
    position: absolute; right: 66px; top: 67px;
    display: flex; font-family: "Jost", sans-serif; font-size: 11.5px;
    color: var(--nav-grey); text-transform: uppercase;
  }
  .main-nav a {
    color: inherit; text-decoration: none; padding: 0 10px;
    border-left: 1px solid var(--nav-divider); line-height: 13px;
  }
  .main-nav a:first-child { border-left: 0; padding-left: 0; }
  .main-nav a:last-child { padding-right: 0; }
  .main-nav a.is-current { color: var(--accent-red); }

  /* Hero */
  .hero {
    position: absolute; left: 28px; top: 114px; width: 826px; height: 420px;
    background: linear-gradient(180deg, #c9c1b4 0%, #3a2c22 40%, #a4582a 70%, #4a4440 100%);
  }
  .hero-caption {
    position: absolute; right: 0; top: 298px; width: 289px; height: 94px;
    background: var(--caption-bg);
    color: #fff; font-family: "Jost", sans-serif; font-size: 23px;
    white-space: nowrap;
    display: flex; align-items: center; padding-left: 22px;
  }
  .hero-band {
    position: absolute; left: 28px; top: 534px; width: 826px; height: 12px;
    background: var(--accent-red);
  }

  /* Intro */
  .intro { position: absolute; left: 28px; top: 567px; width: 486px; }
  .intro h1 {
    font-size: 21px; font-weight: 400; color: var(--ink-brown); line-height: 28px;
  }
  .intro p {
    margin-top: 18px; font-size: 11px; line-height: 17.5px; color: var(--ink);
  }

  /* News */
  .news { position: absolute; left: 566px; top: 568px; width: 260px; }
  .news h2 {
    font-family: "Jost", sans-serif; font-weight: 400; font-size: 14px; color: var(--ink);
  }
  .news-item { margin-top: 13px; font-size: 10.5px; line-height: 13px; color: var(--ink); }
  .news-item + .news-item { margin-top: 11px; }
  .news-item h3 { font-size: 10.5px; font-weight: 400; color: var(--accent-red); }
  .news-item a { color: var(--ink); }

  /* Footer */
  .site-footer {
    position: absolute; left: 28px; top: 724px; width: 826px;
    border-top: 2px solid var(--rule);
    display: flex; justify-content: space-between; align-items: center;
    padding-top: 12px; font-size: 10.5px; color: var(--ink);
  }
  .follow { display: flex; align-items: center; gap: 6px; }
  .follow .label { margin-right: 4px; }
  .follow .social { width: 10px; height: 10px; background: #666; display: inline-block; }
</style>
</head>
<body>
  <div class="backdrop-drawing" role="img" aria-label="Faint architectural floor plan drawing in brown tones"></div>
  <div class="page">
    <header>
      <div class="brand"><span class="brand-mark"></span>QLBRANK WORKS</div>
      <nav class="main-nav">
        <a href="#" class="is-current">Home</a>
        <a href="#">About Us</a>
        <a href="#">Services</a>
        <a href="#">Portfolio</a>
        <a href="#">Career</a>
        <a href="#">Contact Us</a>
      </nav>
    </header>

    <div class="hero" role="img" aria-label="Photo of a meeting room with orange chairs, a white table and a wall of colourful circular plates">
      <div class="hero-caption">Northgate Media Office</div>
    </div>
    <div class="hero-band"></div>

    <section class="intro">
      <h1>Qlbrank Works Design Studios Makes the Process Predictable</h1>
      <p>When something as important as the very space in which your business lives and works is about to be disrupted, you should be confident you've chosen the right space and the best team to ensure a successful project. Rely on Qlbrank Works Design Studios to meet your needs and to make the process predictable. You can be assured that your project goals and objectives will be achieved.</p>
    </section>

    <aside class="news">
      <h2>NEWS</h2>
      <div class="news-item">
        <h3>News Title 1</h3>
        <p>Lorem ipsum dolor sit amet, consectetur adipiscing elit. Mauris vitae dui nunc. Nullam lacus lacus...<a href="#">more</a></p>
      </div>
      <div class="news-item">
        <h3>New Office Location</h3>
        <p>Lorem ipsum dolor sit amet, consectetur adipiscing elit. Mauris vitae dui nunc. Nullam lacus lacus...<a href="#">more</a></p>
      </div>
    </aside>

    <footer class="site-footer">
      <span>© 2011 Qlbrank Works Design Studios.</span>
      <span class="follow"><span class="label">Follow us</span><span class="social"></span><span class="social"></span></span>
    </footer>
  </div>
</body>
</html>
```